Thornbury Spa

We are a large Miami Beach spa and salon. I am still building our website but you can use it as a resource to gain a better understanding of who we are ....www.velloraspa-studio.com.

We offer a comprehensive list of services in hair, nails, massage, skin care, tanning, spray tanning and waxing and we offer high quality products for skin care, tanning and hair. We are open 7 days.

We would like to see a clean and simple menu that looks a lot like the one from "The Spa at Larkwood." In particular, we have a copy of a menu from their West Hollywood, CA location that is just beautiful. In the uploaded content you will see a sampling of that menu. We would like to see greys, blacks, silvers, whites and warm colors like reds and oranges. We specifically attempt to remain gender neutral so that we don't attract only girls (with pink colors and flowers etc). The final design should convey a simple, clean, friendly environment and the final product should be sized such that it is 1.) portable and 2.) inexpensive to print. We will be running thousands of these at a time so cost of printing is a consideration.

The booklet consists of two parts: one part is the standard menu with descriptions of services and products and photos etc (think of this as the sales piece that convinces a potential customer to visit) and will be stapled together like you would expect a small menu to be and should resemble the Larkwood menu. The prices should not be included in this part of the booklet that will be printed and stapled. The other part is a single insert and is removable and replaceable. I want this removable insert placed in the last page of the book in a folder pocket or something else that you can think of so that when it's time to change prices here that I am not throwing away all of the booklets....I am only replacing the inserts at the end of the menu booklet. Please design this single page insert so that should a customer remove it from the booklet and keep it, that it stands alone with our name, logo, website and phone number. This page can and probably will have to be 2 sided.

At the back of the booklet, I also want the polices to be printed in one page (think fine print in any sort of business dealing.)

With regard to the look and feel slider of economical v upmarket...we definitely want to convey we deliver upmarket services at reasonable prices. Think, world class services and products at reasonable, everyday prices.

With regard to the uploaded files:
I uploaded both EPS and TIF formats. The colors in those files are not the palette we want at all. The colors we want use for the circular logo must match the standard colors as depicted in the uploaded file "Thornburytanrooms"

Target Market(s)

The target market is the average 20-35 year old in Miami Beach that cares about their appearance. The range of clientele is quite diverse.

Industry/Entity Type

Environment

Requirements
Must have
• It must have elegant and simple photographs that relate to the services being offered. We are selling a service set and an environment...so this menu should be reflect that goal. The logo should be repeated often throughout the book but in subtle ways.

Stock photos are fine as long as they don't seem obviously stock.

Should not have
• Nothing buddha like. Nothing themed. It should be all inclusive and not seek to identify with any particular group or gender.

Nothing that fits the stereotype of "Miami Beach." We want to represent ourselves in the same category as the best spas in the world because we moving everything we do in that direction. Think class!

```html
<!DOCTYPE html>
<html lang="en">
<head>
<meta charset="utf-8">
<title>Thornbury Spa · Price Insert</title>
<link href="https://fonts.googleapis.com/css2?family=Cabin:wght@400;500&display=swap" rel="stylesheet">
<style>
  :root {
    --bg-center: #3a3c3d;
    --bg-edge: #1c1d1e;
    --ink: #f2f2f2;
    --rule: #6a6c6e;
    --band: #5b5c5d;
    --band-ink: #d4d4d4;
    --tan-green: #1f9a5b;
    --skin-olive: #6b7457;
    --thread-teal: #1d4b5d;
    --accent: #e4572b;
  }
  * { box-sizing: border-box; margin: 0; padding: 0; }
  html, body { width: 1200px; height: 874px; overflow: hidden; }
  body {
    font-family: "Cabin", sans-serif;
    color: var(--ink);
    background: radial-gradient(ellipse 60% 55% at 50% 45%, var(--bg-center), var(--bg-edge));
    position: relative;
  }
  .column { position: absolute; width: 342px; }
  .column--massage { left: 40px; top: 27px; }
  .column--tanning { left: 430px; top: 30px; }
  .column--waxing { left: 811px; top: 27px; }

  .section { margin-bottom: 5px; }
  .section-head, .row {
    display: grid;
    grid-template-columns: minmax(0, 1fr) 66px 82px;
    align-items: center;
  }
  .section-head span, .row span { white-space: nowrap; min-width: 0; }
  .section-head {
    height: 23px;
    border: 1px solid var(--rule);
    border-left: none;
    font-size: 18px;
    padding-right: 2px;
  }
  .section-head span:nth-child(n+2), .row span:nth-child(n+2) { text-align: right; }
  .rows { margin-top: 2px; }
  .row { height: 25px; font-size: 14px; }
  .row--tight .name { letter-spacing: -0.7px; font-size: 13px; }
  .row--tall { height: 44px; align-items: end; padding-bottom: 6px; }
  .row--tall .name { line-height: 18px; }

  .banner {
    height: 24px;
    text-align: center;
    font-size: 20px;
    line-height: 24px;
    letter-spacing: 0.2px;
  }
  .banner--skin { background: var(--skin-olive); margin: 10px 0 16px; }
  .banner--tan { background: var(--tan-green); margin-bottom: 18px; }
  .banner--thread { background: var(--thread-teal); margin: 24px 0 17px; }

  .contact-card {
    position: absolute;
    left: 811px; top: 522px;
    width: 342px; height: 205px;
    border: 1px solid var(--rule);
    text-align: center;
  }
  .contact-card__headline {
    color: var(--accent);
    font-size: 22px;
    line-height: 28px;
    margin-top: 16px;
  }
  .contact-card__rule { height: 1px; background: var(--rule); margin: 11px 8px; }
  .contact-card__info { font-size: 14px; line-height: 18px; }
  .contact-card__web { font-size: 13px; letter-spacing: 2.4px; margin-top: -2px; }

  .footer-band { position: absolute; left: 0; top: 760px; width: 1200px; height: 114px; }
  .footer-web {
    position: absolute; left: 0; top: 808px; width: 1200px;
    text-align: center;
    font-size: 30px;
    letter-spacing: 12px;
    color: var(--band-ink);
    white-space: nowrap;
  }
</style>
</head>
<body>

<div class="column column--massage">
  <div class="section">
    <div class="section-head"><span>Reflexology</span><span>LP</span><span>HG</span></div>
    <div class="rows"><div class="row row--tight"><span class="name">The 45 Minute Reflexology Session</span><span>$100</span><span>$115</span></div></div>
  </div>
  <div class="section">
    <div class="section-head"><span>Thai Massage</span><span>LP</span><span>HG</span></div>
    <div class="rows"><div class="row"><span class="name">The Thai Session (45-60 Minutes)</span><span>$79</span><span>$90</span></div></div>
  </div>
  <div class="section">
    <div class="section-head"><span>Aromatherapy</span><span>LP</span><span>HG</span></div>
    <div class="rows">
      <div class="row"><span class="name">The 75-Minute Sensory Journey</span><span>$119</span><span>$135</span></div>
      <div class="row"><span class="name">The 105-Minute Sensory Journey</span><span>$159</span><span>$185</span></div>
    </div>
  </div>
  <div class="section">
    <div class="section-head"><span>Hot Stone Therapy</span><span>LP</span><span>HG</span></div>
    <div class="rows">
      <div class="row"><span class="name">The 60-Minute Hot Stone Massage</span><span>$109</span><span>$125</span></div>
      <div class="row"><span class="name">The 90-Minute Hot Stone Massage</span><span>$149</span><span>$175</span></div>
    </div>
  </div>
  <div class="section">
    <div class="section-head"><span>Prenatal Massage</span><span>LP</span><span>HG</span></div>
    <div class="rows"><div class="row"><span class="name">The 60-Minute Prenatal Massage</span><span>$99</span><span>$115</span></div></div>
  </div>
  <div class="section">
    <div class="section-head"><span>Shiatsu</span><span>LP</span><span>HG</span></div>
    <div class="rows"><div class="row"><span class="name">The 50-Minute Shiatsu Massage</span><span>$109</span><span>$125</span></div></div>
  </div>

  <div class="banner banner--skin">SKIN CARE MENU</div>

  <div class="section">
    <div class="section-head"><span>Clinical Facial</span><span>LP</span><span>HG</span></div>
    <div class="rows">
      <div class="row"><span class="name">The 30-Minute Express Clinical</span><span>$55</span><span>$65</span></div>
      <div class="row"><span class="name">The 60-Minute Signature Clinical</span><span>$89</span><span>$105</span></div>
    </div>
  </div>
  <div class="section">
    <div class="section-head"><span>Chemical Peel</span><span>LP</span><span>HG</span></div>
    <div class="rows"><div class="row"><span class="name">The Chemical Appeal</span><span>$109</span><span>$125</span></div></div>
  </div>
  <div class="section">
    <div class="section-head"><span>Organic Facial</span><span>LP</span><span>HG</span></div>
    <div class="rows">
      <div class="row row--tight"><span class="name">The 30-Minute Express Organic</span><span>$60</span><span>$70</span></div>
      <div class="row row--tight"><span class="name">The 60-Minute Signature Organic</span><span>$99</span><span>$115</span></div>
    </div>
  </div>
  <div class="section">
    <div class="section-head"><span>Microdermabrasion</span><span>LP</span><span>HG</span></div>
    <div class="rows">
      <div class="row"><span class="name">Microdermabrasion Session</span><span>$109</span><span>$125</span></div>
      <div class="row"><span class="name">Microdermabrasion Series of 5</span><span>$499</span><span></span></div>
      <div class="row"><span class="name">Microdermabrasion Series of 10</span><span>$849</span><span></span></div>
    </div>
  </div>
</div>

<div class="column column--tanning">
  <div class="banner banner--tan">TANNING MENU</div>
  <div class="section">
    <div class="section-head"><span>Custom Airbrush Tanning</span><span>LP</span><span>HG</span></div>
    <div class="rows">
      <div class="row row--tight"><span class="name">Unlimited Infinity Membership (1 month)</span><span>$109</span><span>$125</span></div>
      <div class="row"><span class="name">Custom Infinity Tan (1 session)</span><span>$49</span><span>$55</span></div>
      <div class="row row--tall"><span class="name">Exfoliating Dry Body Scrub &amp;<br>Infinity Tan</span><span>$79</span><span>$90</span></div>
    </div>
  </div>
  <div class="section">
    <div class="section-head"><span>UV Sessions</span><span>LP</span><span>HG</span></div>
    <div class="rows">
      <div class="row row--tight"><span class="name">Single Silver Sessions</span><span>$9</span><span></span></div>
      <div class="row row--tight"><span class="name">Single Gold Sessions</span><span>$14</span><span></span></div>
      <div class="row row--tight"><span class="name">3 Silver Sessions</span><span></span><span></span></div>
      <div class="row row--tight"><span class="name">3 Gold Sessions</span><span></span><span></span></div>
    </div>
  </div>
  <div class="section">
    <div class="section-head"><span>UV Tanning</span><span>LP</span><span>HG</span></div>
    <div class="rows">
      <div class="row"><span class="name">Silver Unlimited 1 week</span><span>$19</span><span>$19</span></div>
      <div class="row"><span class="name">Silver Unlimited 1 month</span><span>$29</span><span>$29</span></div>
      <div class="row"><span class="name">Silver Unlimited 3 months</span><span>$79</span><span>$79</span></div>
      <div class="row"><span class="name">Silver Unlimited 6 months</span><span>$139</span><span>$139</span></div>
      <div class="row"><span class="name">Silver Unlimited 12 months</span><span>$249</span><span>$249</span></div>
      <div class="row"><span class="name">Gold Unlimited 1 week</span><span>$29</span><span>$29</span></div>
      <div class="row"><span class="name">Gold Unlimited 1 month</span><span>$39</span><span>$39</span></div>
      <div class="row"><span class="name">Gold Unlimited 3 months</span><span>$99</span><span>$99</span></div>
      <div class="row"><span class="name">Gold Unlimited 6 months</span><span>$189</span><span>$189</span></div>
      <div class="row"><span class="name">Gold Unlimited 12 months</span><span>$349</span><span>$349</span></div>
    </div>
  </div>

  <div class="banner banner--thread">THREADING &amp; WAXING MENU</div>

  <div class="section">
    <div class="section-head"><span>Threading</span><span>LP</span><span>HG</span></div>
    <div class="rows">
      <div class="row"><span class="name">Eyebrow</span><span>$15</span><span>$17</span></div>
      <div class="row"><span class="name">Upper Lip</span><span>$10</span><span>$12</span></div>
      <div class="row"><span class="name">Facial</span><span>from $25</span><span>from $30</span></div>
    </div>
  </div>
</div>

<div class="column column--waxing">
  <div class="section">
    <div class="section-head"><span>Waxing</span><span>LP</span><span>HG</span></div>
    <div class="rows">
      <div class="row"><span class="name">Eyebrows</span><span>$15</span><span>$18</span></div>
      <div class="row"><span class="name">Upper Lip</span><span>$8</span><span>$10</span></div>
      <div class="row"><span class="name">Nose</span><span>$8</span><span>$10</span></div>
      <div class="row"><span class="name">Chin</span><span>$8</span><span>$10</span></div>
      <div class="row"><span class="name">Chest</span><span>from $20</span><span>from $24</span></div>
      <div class="row"><span class="name">Stomach</span><span>from $17</span><span>from $20</span></div>
      <div class="row"><span class="name">Back</span><span>from $40</span><span>from $45</span></div>
      <div class="row"><span class="name">Underarm</span><span>$15</span><span>$18</span></div>
      <div class="row"><span class="name">Deep Bikini</span><span>$25</span><span>$30</span></div>
      <div class="row"><span class="name">Partial Brazilian</span><span>$35</span><span>$40</span></div>
      <div class="row"><span class="name">Full Brazilian</span><span>$45</span><span>$50</span></div>
      <div class="row"><span class="name">Buttocks (Female)</span><span>$10</span><span>$10</span></div>
      <div class="row"><span class="name">Buttocks (Male)</span><span>from $25</span><span>from $29</span></div>
      <div class="row"><span class="name">Half Arm</span><span>$15</span><span>$18</span></div>
      <div class="row"><span class="name">Full Arm</span><span>$22</span><span>$26</span></div>
      <div class="row"><span class="name">Half Leg</span><span>from $25</span><span>from $30</span></div>
      <div class="row"><span class="name">Full Leg</span><span>from $35</span><span>from $40</span></div>
    </div>
  </div>
</div>

<div class="contact-card">
  <p class="contact-card__headline">CONSULTATIONS ARE<br>ALWAYS FREE</p>
  <div class="contact-card__rule"></div>
  <p class="contact-card__info">Call Us: 305.555.0148<br>Palmetto Shores, 2400 Harbor Lane #1<br>Miami Beach, Florida</p>
  <div class="contact-card__rule"></div>
  <p class="contact-card__web">www.velloraspa-studio.com</p>
</div>

<svg class="footer-band" viewBox="0 0 1200 114" preserveAspectRatio="none" aria-hidden="true">
  <defs>
    <linearGradient id="bandShade" x1="0" y1="0" x2="0" y2="1">
      <stop offset="0" stop-color="#6a6b6c"/>
      <stop offset="1" stop-color="#505152"/>
    </linearGradient>
  </defs>
  <path d="M0 8 C300 22 700 30 1200 26 L1200 114 L0 114 Z" fill="url(#bandShade)"/>
</svg>
<p class="footer-web">www.velloraspa-studio.com</p>

</body>
</html>
```